KRL Stationery Design Project

Dear Designers,
We need a new stationery design for company to match our new logo.
Designers should provide a design for the following:
1. Business Card: 3.5x2 Inches.
2. Letterhead: A4 size.
3. Envelops: 25x35.5 Cm.
You can keep the Arabic name at the bottom of the logo Or you can use the separate attached Arabic Name.
Please refer to the attached logo guide for design information.
Sample Business Card information:
Name: Tarek Sowan
Position: Operation Manager
Tel: +966 920007164 Ex. 500
Fax: +966 (3)8842617
Mob: +966 (5)00263817
email: tarek@krl-example.com.sa
URL: www.krl-example.com.sa
Address:
Nakheel Heights, Suite 718
Zayed bin Omar Str.
Khobar, 31847
Saudi Arabia
Updates
Dear All,
Please note, we had uploaded our logo along with Arabic writing in Adobe illustrator format (.ai).
Regards,
Karim
Dear All,
A sample data for the business card had been added as per your request.
Regards,
Karim

```html
<!DOCTYPE html>
<html lang="en">
<head>
<meta charset="utf-8">
<title>KRL Business Card</title>
<link href="https://fonts.googleapis.com/css2?family=Open+Sans:ital,wght@0,400;0,700;1,700&display=swap" rel="stylesheet">
<style>
  :root {
    --navy: #132f55;
    --grey: #9a9b9d;
    --ink: #3a3a3c;
    --card: #ffffff;
    --backdrop: #e6e7e9;
  }
  * { margin: 0; padding: 0; box-sizing: border-box; }
  html, body {
    width: 960px;
    height: 1200px;
    overflow: hidden;
    background: var(--backdrop);
    font-family: "Open Sans", Arial, sans-serif;
  }
  .card {
    position: absolute;
    width: 840px;
    height: 478px;
    background: var(--card);
    border-radius: 28px;
    overflow: hidden;
  }
  .card--front { left: 55px; top: 78px; }
  .card--back { left: 57px; top: 625px; }

  .brand {
    position: absolute;
    display: flex;
    align-items: center;
    color: var(--navy);
    font-weight: 700;
    letter-spacing: 2px;
  }
  .brand__mark {
    background: var(--navy);
    border-radius: 50%;
  }
  .card--front .brand { left: 110px; top: 150px; font-size: 96px; gap: 22px; }
  .card--front .brand__mark { width: 34px; height: 34px; }
  .card--back .brand { left: 0; right: 0; top: 160px; justify-content: center; font-size: 120px; gap: 28px; }
  .card--back .brand__mark { width: 42px; height: 42px; }

  .divider {
    position: absolute;
    left: 515px;
    top: 102px;
    width: 3px;
    height: 185px;
    background: var(--ink);
  }
  .person {
    position: absolute;
    left: 545px;
    top: 98px;
    color: var(--navy);
  }
  .person__name { font-size: 25px; line-height: 32px; }
  .person__role { font-size: 19px; line-height: 26px; }

  .contact {
    position: absolute;
    left: 545px;
    top: 178px;
    list-style: none;
    color: var(--ink);
    font-size: 18.5px;
    line-height: 28px;
  }
  .contact__label { font-weight: 700; font-style: italic; }

  .wave { position: absolute; left: 0; top: 0; width: 840px; height: 478px; }

  .address {
    position: absolute;
    left: 51px;
    top: 393px;
    color: #ffffff;
    font-size: 19px;
    line-height: 28px;
  }
</style>
</head>
<body>
  <section class="card card--front">
    <svg class="wave" viewBox="0 0 840 478" aria-hidden="true">
      <path fill="var(--grey)" d="M175,340 C300,342 380,385 440,402 C600,428 720,380 840,340 L840,362 C700,402 560,440 420,414 C320,380 250,350 175,340Z"/>
      <path fill="var(--navy)" d="M0,380 C120,342 250,350 420,414 C560,440 700,402 840,362 L840,478 L0,478Z"/>
    </svg>

    <div class="brand"><span class="brand__mark"></span>KRL</div>

    <div class="divider"></div>

    <div class="person">
      <p class="person__name">Your Name</p>
      <p class="person__role">Designation</p>
    </div>

    <ul class="contact">
      <li><span class="contact__label">t</span> : 123-123-1234</li>
      <li><span class="contact__label">f</span> : 123-123-1234</li>
      <li><span class="contact__label">e</span> : info@krl-example.com.sa</li>
      <li><span class="contact__label">w</span> : www.krl-example.com.sa</li>
    </ul>

    <address class="address" style="font-style: normal;">
      1234, Suite# 123<br>
      Street Name, Country Code
    </address>
  </section>

  <section class="card card--back">
    <div class="brand"><span class="brand__mark"></span>KRL</div>
  </section>
</body>
</html>
```